Private Investigation Business Card Design

I need a business card for a new private investigation company named Brisk Inquiries. I perform mainly surveillance jobs, vehicle repossessions, document serves etc. The final design should aim for a professional look. The logo has a magnifying glass with stick man arms and legs and is in a running action to show the "Brisk" aspect of the name. If the colour scheme could remain the same as the website www.briskinquiries-demo.com.au with silvers,blacks and a couple electric blue highlights.
Industry/Entity Type
Business
Contact Information for Business Card
Morgan Kellaway
Brisk Inquiries
0487316204
PO Box 58, Carnwell NSW 2291
info@briskinquiries-demo.com.au
www.briskinquiries-demo.com.au
Look and feel

```html
<!DOCTYPE html>
<html lang="en">
<head>
<meta charset="utf-8">
<title>Brisk Inquiries – Business Card</title>
<link href="https://fonts.googleapis.com/css2?family=Play:wght@400;700&display=swap" rel="stylesheet">
<style>
  :root {
    --page-bg: #d9d4ce;
    --panel-dark: #161616;
    --panel-mid: #3a3a3c;
    --frost-light: #f1f1f0;
    --frost-mid: #cfd0cf;
    --ring-light: #e8e8e8;
    --ring-dark: #6d6d6d;
    --name-text: #e4e4e4;
    --detail-text: #b9b9b9;
    --brand-text: #2b2b2d;
  }
  html, body {
    margin: 0;
    padding: 0;
    width: 1200px;
    height: 969px;
    overflow: hidden;
    background: var(--page-bg);
    font-family: "Play", sans-serif;
  }
  .card {
    position: absolute;
    left: 100px;
    top: 201px;
    width: 1000px;
    height: 567px;
    box-shadow: 0 12px 40px rgba(0,0,0,0.25);
  }
  .card-art {
    position: absolute;
    inset: 0;
    width: 1000px;
    height: 567px;
  }
  .holder-name {
    position: absolute;
    left: 82px;
    top: 88px;
    margin: 0;
    font-size: 29px;
    font-weight: 700;
    letter-spacing: 0.5px;
    color: var(--name-text);
  }
  .postal-address {
    position: absolute;
    left: 82px;
    top: 322px;
    margin: 0;
    font-style: normal;
    font-size: 23px;
    line-height: 33px;
    color: var(--detail-text);
  }
  .contact-list {
    position: absolute;
    left: 82px;
    top: 396px;
    margin: 0;
    padding: 0;
    list-style: none;
    font-size: 22px;
    color: var(--detail-text);
  }
  .contact-list li {
    display: flex;
    align-items: center;
    height: 40px;
  }
  .contact-list svg {
    width: 22px;
    height: 22px;
    margin-right: 14px;
    fill: var(--detail-text);
  }
  .contact-list .phone { font-size: 24px; }
  .brand-name {
    position: absolute;
    left: 560px;
    top: 240px;
    width: 420px;
    margin: 0;
    text-align: center;
    font-size: 52px;
    font-weight: 700;
    letter-spacing: 1px;
    color: var(--brand-text);
  }
</style>
</head>
<body>
  <article class="card">
    <svg class="card-art" viewBox="0 0 1000 567" aria-hidden="true">
      <defs>
        <linearGradient id="frostFill" x1="0" y1="0" x2="1" y2="1">
          <stop offset="0" stop-color="var(--frost-light)"/>
          <stop offset="1" stop-color="var(--frost-mid)"/>
        </linearGradient>
        <linearGradient id="darkPanel" x1="0" y1="0" x2="1" y2="1">
          <stop offset="0" stop-color="var(--panel-mid)"/>
          <stop offset="0.55" stop-color="var(--panel-dark)"/>
          <stop offset="1" stop-color="#262627"/>
        </linearGradient>
        <linearGradient id="ringMetal" x1="0" y1="0" x2="0" y2="1">
          <stop offset="0" stop-color="var(--ring-dark)"/>
          <stop offset="0.35" stop-color="var(--ring-light)"/>
          <stop offset="0.7" stop-color="var(--ring-dark)"/>
          <stop offset="1" stop-color="var(--ring-light)"/>
        </linearGradient>
        <mask id="panelCut">
          <rect width="1000" height="567" fill="#fff"/>
          <circle cx="860" cy="273" r="395" fill="#000"/>
        </mask>
      </defs>
      <rect class="frost-surface" width="1000" height="567" fill="url(#frostFill)"/>
      <rect class="dark-panel" width="1000" height="567" fill="url(#darkPanel)" mask="url(#panelCut)"/>
      <circle class="outer-ring" cx="860" cy="273" r="385" fill="none" stroke="url(#ringMetal)" stroke-width="20"/>
      <circle class="inner-ring" cx="860" cy="273" r="352" fill="none" stroke="#bdbdbd" stroke-width="4" opacity="0.7"/>
    </svg>

    <h1 class="holder-name">Morgan Kellaway</h1>

    <address class="postal-address">PO Box 58<br>Carnwell NSW 2291</address>

    <ul class="contact-list">
      <li class="phone">
        <svg viewBox="0 0 24 24"><path d="M6.6 10.8a15.1 15.1 0 0 0 6.6 6.6l2.2-2.2c.3-.3.7-.4 1-.2 1.1.4 2.3.6 3.6.6.6 0 1 .4 1 1V20c0 .6-.4 1-1 1A17 17 0 0 1 3 4c0-.6.4-1 1-1h3.5c.6 0 1 .4 1 1 0 1.3.2 2.5.6 3.6.1.3 0 .7-.2 1z"/></svg>
        0487 316 204
      </li>
      <li class="email">
        <svg viewBox="0 0 24 24"><path d="M2 5h20v14H2z M4 7v.4l8 5 8-5V7z" fill-rule="evenodd"/></svg>
        info@briskinquiries-demo.com.au
      </li>
      <li class="web">
        <svg viewBox="0 0 24 24"><path d="M12 2a10 10 0 1 0 0 20 10 10 0 0 0 0-20zm-1 17.9A8 8 0 0 1 4.1 11H7c.1 2.9.8 6 4 8.9zM7 9H4.3A8 8 0 0 1 11 4.1C8.4 6 7.3 7.6 7 9zm6-4.9A8 8 0 0 1 19.7 9H17c-.3-1.4-1.4-3-4-4.9zM9 11h6c-.1 2.6-1 5-3 7-2-2-2.9-4.4-3-7zm0-2c.3-1.4 1.2-3 3-4.6 1.8 1.6 2.7 3.2 3 4.6zm4 10.9c3.2-2.9 3.9-6 4-8.9h2.9a8 8 0 0 1-6.9 8.9z"/></svg>
        www.briskinquiries-demo.com.au
      </li>
    </ul>

    <p class="brand-name">Brisk Inquiries</p>
  </article>
</body>
</html>
```